Dental office stationary (letterhead, envelopes), business cards, presentation folders

Nothing too dental outside of the logo. I will need all stationary, presentation folders, business cards. Would prefer to stay in the colors of the logo

Gordon Patel, DDS
Bright Haven Dental Implant Center
555-318-2790
info@brighthavendental.example
4817 NW Maple Crest Rd Unit B
Harbor Glen, ZZ 00000

Also need appointment date and time
And cancellation policy
I want it to say “kindly ask for
A 48hr cancellation policy to avoid incurring a cancellation fee”

Industry/Entity Type

Dental

Colors
0054AA
0677BA
7BADD7
CADEEF
E8F1F8

Requirements
Must have
• Name of your office, name of doctor, address, phone number
Should not have
• Too much tooth/dental. Only the tooth in logo

```html
<!DOCTYPE html>
<html lang="en">
<head>
<meta charset="utf-8">
<title>Bright Haven Dental Implant Center – Stationery Set</title>
<link href="https://fonts.googleapis.com/css2?family=Arimo:wght@400;700&family=Libre+Baskerville:wght@700&display=swap" rel="stylesheet">
<style>
:root{
  --blue:#0677BA;
  --deep:#0054AA;
  --light:#7BADD7;
  --pale:#CADEEF;
  --mist:#E8F1F8;
  --teal:#2CB89B;
  --teal-ink:#1E8F9A;
  --paper:#F6F4F5;
  --ink:#3A3A3A;
  --stage:#3C3C3E;
}
*{margin:0;padding:0;box-sizing:border-box}
html,body{width:1200px;height:292px;overflow:hidden;background:var(--stage);font-family:Arimo,Arial,sans-serif;color:var(--ink)}
.canvas{position:relative;width:1200px;height:292px}
.piece{position:absolute;overflow:hidden;box-shadow:0 2px 5px rgba(0,0,0,.45)}
.piece svg.wash{position:absolute;inset:0;width:100%;height:100%}
.brand{position:absolute;text-align:center;white-space:nowrap;line-height:1}
.brand .name{font-family:Arimo,Arial,sans-serif;font-weight:400;letter-spacing:.02em;color:var(--blue);display:flex;align-items:center;justify-content:center;gap:.25em}
.brand .name::before{content:"";width:.45em;height:.45em;border-radius:50%;background:currentColor;display:inline-block}
.brand .sub{font-family:Arimo,Arial,sans-serif;letter-spacing:.22em;color:#6f7c88;margin-top:.3em}
.brand.on-dark .name,.brand.on-dark .sub{color:#fff}
.tiny{position:absolute;font-size:3px;line-height:1.35;color:#333;white-space:nowrap}
.tiny.white{color:#fff}
.ico{display:inline-block;width:2.4px;height:2.4px;border-radius:50%;background:currentColor;margin-right:1.2px;vertical-align:middle}

/* business card front */
.card-front{left:25px;top:26px;width:125px;height:71px;background:#fff;border-radius:3px}
.card-front .doctor{position:absolute;right:7px;top:10px;font-family:"Libre Baskerville",serif;font-size:4.4px;color:#fff;text-align:right}
.card-front .doctor small{display:block;font-family:Arimo,sans-serif;font-size:2.4px;font-weight:400;margin-top:.6px}
/* card back */
.card-back{left:22px;top:110px;width:128px;height:73px;background:var(--teal);border-radius:3px}
/* appointment */
.appt{left:22px;top:199px;width:128px;height:73px;background:#fff;border-radius:3px}
.appt h3{position:absolute;top:7px;width:100%;text-align:center;font-size:4.8px;font-weight:700;color:var(--blue)}
.appt .rows{position:absolute;left:7px;right:7px;top:17px}
.appt .row{display:flex;align-items:flex-end;font-size:3.6px;color:var(--blue);height:8px}
.appt .row .dots{flex:1;border-bottom:.4px dotted #777;margin:0 1px 1px}
.appt .row .ampm{font-size:2.4px;margin-left:1px}
.appt .web{position:absolute;left:0;right:0;top:56px;height:6px;background:var(--blue);color:#fff;font-size:3.4px;letter-spacing:.15em;text-align:center;line-height:6px}
.appt .policy{position:absolute;left:0;right:0;top:65px;font-size:2.6px;text-align:center;color:#333}
/* letterhead */
.letter{left:170px;top:25px;width:175px;height:247px;background:var(--paper)}
.letter .greet{position:absolute;left:17px;top:60px;font-size:4.6px;color:#333}
.letter .body{position:absolute;left:17px;top:74px;width:144px;font-size:2.9px;line-height:1.45;color:#555;text-align:justify}
.letter .body p{margin-bottom:4px}
.letter .sign{position:absolute;left:17px;top:168px;font-size:2.9px;color:#555}
.letter .sign .line{width:22px;height:.6px;background:#333;margin:6px 0 7px}
.letter .sign b{display:block;font-weight:400;font-size:3.6px;color:#333}
/* envelopes */
.env-back{left:367px;top:53px;width:196px;height:89px;background:var(--paper)}
.env-front{left:366px;top:162px;width:197px;height:89px;background:var(--paper)}
/* folder closed */
.folder-closed{left:580px;top:61px;width:292px;height:183px;background:#fff}
.folder-closed .spine{position:absolute;left:0;top:0;width:146px;height:100%;background:linear-gradient(135deg,#1a86cf,var(--blue) 60%,#0a6db0)}
/* folder open */
.folder-open{left:883px;top:62px;width:292px;height:183px;background:linear-gradient(90deg,#f4f4f4,#e9e9e9 49.5%,#dcdcdc 50%,#f2f2f2)}
</style>
</head>
<body>
<div class="canvas">

  <section class="piece card-front" aria-label="Business card, front">
    <svg class="wash" viewBox="0 0 125 71" preserveAspectRatio="none">
      <path d="M58,0 Q66,36 72,71 L125,71 L125,0Z" fill="var(--blue)"/>
      <path d="M58,0 Q66,36 72,71" fill="none" stroke="var(--teal)" stroke-width="1"/>
    </svg>
    <div class="brand" style="left:4px;top:32px;width:54px">
      <div class="name" style="font-size:6.4px">BRIGHT HAVEN</div>
      <div class="sub" style="font-size:1.6px">DENTAL IMPLANT CENTER</div>
    </div>
    <div class="doctor">GORDON PATEL<small>DDS</small></div>
    <div class="tiny white" style="right:7px;top:38px;text-align:right;font-size:2.6px">4817 NW Maple Crest Rd Unit B<br>Harbor Glen, ZZ 00000</div>
    <div class="tiny white" style="right:7px;top:49px;text-align:right;font-size:2.6px">555-318-2790 <span class="ico"></span><br>info@brighthavendental.example <span class="ico"></span><br>www.brighthavendental.example <span class="ico"></span></div>
  </section>

  <section class="piece card-back" aria-label="Business card, back">
    <div class="brand" style="left:0;right:0;top:31px">
      <div class="name" style="font-size:10px;color:var(--teal-ink)">BRIGHT HAVEN</div>
      <div class="sub" style="font-size:2.6px;color:var(--teal-ink)">DENTAL IMPLANT CENTER</div>
    </div>
  </section>

  <section class="piece appt" aria-label="Appointment card">
    <h3>Next Appointment</h3>
    <div class="rows">
      <div class="row">Date :<span class="dots"></span>Time :<span class="dots"></span><span class="ampm">AM/PM</span></div>
      <div class="row">Date :<span class="dots"></span>Time :<span class="dots"></span><span class="ampm">AM/PM</span></div>
      <div class="row">Date :<span class="dots"></span>Time :<span class="dots"></span><span class="ampm">AM/PM</span></div>
      <div class="row">Date :<span class="dots"></span>Time :<span class="dots"></span><span class="ampm">AM/PM</span></div>
    </div>
    <div class="web">www.brighthavendental.example</div>
    <div class="policy">kindly ask for A 48hr cancellation policy to avoid incurring a cancellation fee</div>
  </section>

  <section class="piece letter" aria-label="Letterhead">
    <svg class="wash" viewBox="0 0 175 247" preserveAspectRatio="none">
      <path d="M82,247 Q150,220 175,160 L175,247Z" fill="var(--teal)"/>
      <path d="M92,247 Q155,222 175,168 L175,247Z" fill="var(--blue)"/>
    </svg>
    <div class="brand" style="left:16px;top:19px">
      <div class="name" style="font-size:6px">BRIGHT HAVEN</div>
      <div class="sub" style="font-size:1.4px">DENTAL IMPLANT CENTER</div>
    </div>
    <div class="tiny" style="left:120px;top:12px;font-size:2.6px">4817 NW Maple Crest Rd Unit B<br>Harbor Glen, ZZ 00000<br><span style="color:var(--blue)"><span class="ico"></span>555-318-2790<br><span class="ico"></span>info@brighthavendental.example</span></div>
    <div class="greet">Dear Mr. Lowell,</div>
    <div class="body">
      <p>Thank you for choosing our practice for your implant care. This letter confirms the plan we discussed at your recent visit and the steps that follow.</p>
      <p>Our team will contact you to set your first treatment date. Please bring your current medication list and any recent dental records.</p>
      <p>If you have questions before your visit, call our front desk or send us an email and we will reply within one business day.</p>
      <p>We look forward to seeing you soon and helping you restore a confident, comfortable smile for years to come.</p>
    </div>
    <div class="sign">Sincerely,<div class="line"></div><b>Alan Reyes</b>CEO/ Founder</div>
    <div class="tiny white" style="right:7px;bottom:5px;font-size:2.6px">www.brighthavendental.example</div>
  </section>

  <section class="piece env-back" aria-label="Envelope, back">
    <svg class="wash" viewBox="0 0 196 89" preserveAspectRatio="none">
      <path d="M0,0 L196,0 L196,2 L190,26 Q188,33 180,33 L16,33 Q8,33 6,26 L0,2Z" fill="var(--blue)"/>
    </svg>
    <div class="brand on-dark" style="left:0;right:0;top:15px">
      <div class="name" style="font-size:7px">BRIGHT HAVEN</div>
      <div class="sub" style="font-size:1.7px">DENTAL IMPLANT CENTER</div>
    </div>
  </section>

  <section class="piece env-front" aria-label="Envelope, front">
    <svg class="wash" viewBox="0 0 197 89" preserveAspectRatio="none">
      <path d="M92,89 Q175,70 197,2 L197,89Z" fill="var(--teal)"/>
      <path d="M104,89 Q180,72 197,12 L197,89Z" fill="var(--blue)"/>
    </svg>
    <div class="brand" style="left:12px;top:18px">
      <div class="name" style="font-size:6px">BRIGHT HAVEN</div>
      <div class="sub" style="font-size:1.4px">DENTAL IMPLANT CENTER</div>
    </div>
    <div class="tiny" style="left:11px;top:67px;font-size:2.6px">4817 NW Maple Crest Rd Unit B<br>Harbor Glen, ZZ 00000<br><span style="color:var(--blue)"><span class="ico"></span>555-318-2790<br><span class="ico"></span>info@brighthavendental.example</span></div>
    <div class="tiny white" style="right:7px;bottom:4px;font-size:2.6px">www.brighthavendental.example</div>
  </section>

  <section class="piece folder-closed" aria-label="Presentation folder, outside">
    <div class="spine"></div>
    <svg class="wash" viewBox="0 0 292 183" preserveAspectRatio="none">
      <path d="M175,183 Q268,176 292,108 L292,183Z" fill="var(--teal)"/>
      <path d="M186,183 Q272,178 292,118 L292,183Z" fill="var(--blue)"/>
    </svg>
    <div class="brand" style="left:146px;width:146px;top:80px">
      <div class="name" style="font-size:12px">BRIGHT HAVEN</div>
      <div class="sub" style="font-size:3px">DENTAL IMPLANT CENTER</div>
    </div>
    <div class="tiny white" style="left:13px;top:154px;font-size:3px">4817 NW Maple Crest Rd Unit B<br>Harbor Glen, ZZ 00000<br><span class="ico"></span>555-318-2790<br><span class="ico"></span>info@brighthavendental.example</div>
    <div class="tiny white" style="left:92px;top:168px;font-size:3px">www.brighthavendental.example</div>
  </section>

  <section class="piece folder-open" aria-label="Presentation folder, inside">
    <svg class="wash" viewBox="0 0 292 183" preserveAspectRatio="none">
      <path d="M0,110 L128,110 Q136,110 139,118 L146,183 L0,183Z" fill="var(--blue)"/>
      <path d="M292,110 L164,110 Q156,110 153,118 L146,183 L292,183Z" fill="var(--blue)"/>
    </svg>
    <div class="brand on-dark" style="left:0;width:140px;top:140px">
      <div class="name" style="font-size:10px">BRIGHT HAVEN</div>
      <div class="sub" style="font-size:2.5px">DENTAL IMPLANT CENTER</div>
    </div>
    <div class="brand on-dark" style="left:152px;width:140px;top:140px">
      <div class="name" style="font-size:10px">BRIGHT HAVEN</div>
      <div class="sub" style="font-size:2.5px">DENTAL IMPLANT CENTER</div>
    </div>
  </section>

</div>
</body>
</html>
```